Northfield Builders Guild Business card

We are looking for a new business card design with photo included.
Our business is a nonprofit construction contractor membership organization. We offer business education, assist with business setup and licensing, provide safety training, and provide a member directory.
URL: www.builderslinkguild.org
Color code:
CMYK: 0 cyan, 42 magenta, 100 yellow, 0 black for Print.
Hexidecimal: #FF9900
RGB: R 255; G 153; B 0

```html
<!DOCTYPE html>
<html lang="en">
<head>
<meta charset="utf-8">
<title>Northfield Builders Guild Business Card</title>
<link href="https://fonts.googleapis.com/css2?family=Jost:wght@400;700&display=swap" rel="stylesheet">
<style>
  :root {
    --backdrop: #8b8b8b;
    --charcoal: #353435;
    --orange: #ff9900;
    --white: #ffffff;
  }
  * { margin: 0; padding: 0; box-sizing: border-box; }
  html, body {
    width: 1200px; height: 1200px; overflow: hidden;
    background: var(--backdrop);
    font-family: "Jost", sans-serif;
  }
  .card {
    position: absolute; left: 262px; width: 686px; height: 392px;
    box-shadow: 0 18px 30px rgba(0,0,0,0.25);
  }
  .card-front { top: 165px; display: flex; background: var(--white); }
  .card-back { top: 653px; background: var(--charcoal); display: flex; align-items: center; justify-content: center; }
  .contact-panel {
    width: 289px; height: 100%; background: var(--charcoal);
    color: var(--white); padding: 84px 0 0 41px;
  }
  .accent-stripe { width: 8px; height: 100%; background: var(--orange); }
  .brand-panel { flex: 1; display: flex; align-items: center; justify-content: center; }
  .person-name { color: var(--orange); font-weight: 700; font-size: 24px; line-height: 1; letter-spacing: 0.2px; }
  .person-title { color: var(--orange); font-size: 16px; margin-top: 4px; }
  .address { font-size: 16px; line-height: 20px; margin-top: 24px; }
  .contact-list { list-style: none; margin-top: 22px; font-size: 16px; line-height: 20px; }
  .contact-list li { display: flex; align-items: center; gap: 7px; }
  .contact-list svg { width: 12px; height: 12px; flex: none; fill: var(--orange); }
  .brand-name {
    font-weight: 700; font-size: 34px; line-height: 1.05; text-align: center;
    text-transform: uppercase; letter-spacing: 0.5px;
  }
  .brand-name-front { color: var(--charcoal); }
  .brand-name-back { color: var(--orange); font-size: 42px; }
</style>
</head>
<body>
  <section class="card card-front">
    <div class="contact-panel">
      <h1 class="person-name">DANIEL REEVES</h1>
      <p class="person-title">President</p>
      <p class="address">2450 NW Alder St.,<br>Suite #210<br>Salem, OR 97301</p>
      <ul class="contact-list">
        <li><svg viewBox="0 0 12 12"><path d="M2.5 0.5l2 2.5-1.2 1.3c.6 1.6 1.9 2.9 3.4 3.5l1.3-1.2 2.5 2-1.2 2.4C5 10.5 1.5 7 .2 1.7z"/></svg>(555) 318-2064</li>
        <li><svg viewBox="0 0 12 12"><path d="M3 0h6v12H3zM4 1.5v8h4v-8zM5.5 10.3h1v1h-1z" fill-rule="evenodd"/></svg>555.207.4417</li>
        <li><svg viewBox="0 0 12 12"><path d="M0 2.5h12v7H0zM1 3.5l5 3.5 5-3.5z"/></svg>help@nbguild.org</li>
        <li><svg viewBox="0 0 12 12"><circle cx="6" cy="6" r="6"/></svg>www.builderslinkguild.org</li>
      </ul>
    </div>
    <div class="accent-stripe"></div>
    <div class="brand-panel">
      <p class="brand-name brand-name-front">Northfield<br>Builders Guild</p>
    </div>
  </section>
  <section class="card card-back">
    <p class="brand-name brand-name-back">Northfield<br>Builders Guild</p>
  </section>
</body>
</html>
```